Web Design

Looking for web designer for total service. We would like to make it in English and Japanese for now. Also need to make Tablet version. Our website is www.corvelpicks.com and www.brindaleads .com

```html
<!DOCTYPE html>
<html lang="en">
<head>
<meta charset="utf-8">
<title>Brindale Trading</title>
<link href="https://fonts.googleapis.com/css2?family=Lato:wght@400;700;900&display=swap" rel="stylesheet">
<style>
:root{
  --brown:#6b4a2b;
  --green:#2f7a1f;
  --green-dark:#2a6b1b;
  --orange:#ef5a1c;
  --ink:#222;
  --text:#444;
  --light:#f1f1f1;
  --box:#ededed;
  --box-active:#dcdcdc;
  --footer:#333;
  --footer-text:#c9c9c9;
}
*{box-sizing:border-box;margin:0;padding:0}
html,body{width:1200px;height:2350px;overflow:hidden}
body{font-family:'Lato',sans-serif;color:var(--text);background:#fff;position:relative}

/* header */
.site-header{height:125px;position:relative}
.brand{position:absolute;left:75px;top:30px;display:flex;align-items:center;gap:10px}
.brand-dot{width:22px;height:22px;border-radius:50%;background:var(--green)}
.brand-name{font-weight:900;font-size:24px;color:var(--brown);letter-spacing:1px;line-height:1.1}
.top-phone{position:absolute;left:868px;top:25px;display:flex;align-items:center;gap:10px;color:var(--green);font-size:19px;font-weight:700}
.lang{position:absolute;left:1060px;top:28px;display:flex;align-items:center;gap:8px;font-size:12px;color:#555}
.flag{width:22px;height:13px;background:#2d3f8f}
.main-nav{position:absolute;left:278px;top:75px;display:flex;align-items:center}
.main-nav a{font-size:13px;color:#222;text-decoration:none;padding:0 17px;line-height:35px;text-transform:uppercase}
.main-nav a.active{background:var(--brown);color:#fff}

/* hero */
.hero{height:532px;background:linear-gradient(90deg,#f4f2f4 0%,#efedf1 45%,#e9e6ec 100%);position:relative;overflow:hidden}
.hero-photo{position:absolute;left:440px;top:0;width:760px;height:532px;background:linear-gradient(100deg,rgba(255,255,255,0) 0%,#e8d7c0 30%,#d9b98f 55%,#e6cfa8 80%,#ece7ee 100%)}
.hero-text{position:absolute;left:75px;top:160px;width:460px}
.hero-title{font-size:37px;font-weight:700;color:var(--brown);line-height:1.1;width:320px}
.hero-sub{margin-top:14px;font-size:18.5px;font-weight:700;color:#4a4a4a;line-height:1.55;width:460px}
.dots{position:absolute;left:75px;top:465px;display:flex;gap:6px}
.dots span{width:11px;height:11px;border-radius:50%;background:#666}
.dots span.on{background:var(--green)}

/* about */
.about{height:393px;text-align:center;padding-top:55px}
.about h2{font-size:33px;font-weight:700;color:var(--ink)}
.about h3{margin-top:22px;font-size:24px;font-weight:700;color:var(--brown)}
.about p{width:1050px;margin:22px auto 0;font-size:15.5px;line-height:1.72;color:#333}
.btn{display:inline-block;margin-top:40px;background:var(--green);color:#fff;font-weight:700;font-size:17px;width:180px;height:49px;line-height:49px;text-decoration:none}

/* services */
.services{height:340px;background:var(--light);padding-top:50px}
.service-row{display:flex;justify-content:space-between;width:1050px;margin:0 auto}
.service{width:330px;height:243px;display:flex;align-items:center;justify-content:center;text-align:center;color:#fff;font-weight:700;font-size:19px;line-height:1.45;padding:0 14px}
.service.marketing{padding:0 48px}
.service.food{background:linear-gradient(160deg,#3a3a2e,#6a5a44 55%,#2c2f2c)}
.service.catering{background:linear-gradient(160deg,#b88a5a,#d9c3a0 45%,#8a6a48)}
.service.marketing{background:linear-gradient(160deg,#3a5472,#5f7791 55%,#2c3e57)}

/* products */
.products{height:445px;text-align:center;padding-top:30px;position:relative}
.products h2{font-size:33px;font-weight:700;color:var(--ink)}
.product-row{position:absolute;left:105px;top:105px;width:990px;display:flex;justify-content:space-between}
.product{width:240px;text-align:center}
.product-shot{width:110px;height:245px;margin:0 auto;border-radius:6px}
.product-name{margin-top:18px;font-size:19px;font-weight:700;color:var(--orange)}
.p-banana{background:linear-gradient(180deg,#c9a878 0%,#e6d463 55%,#caa878 100%)}
.p-acai{background:linear-gradient(180deg,#cfae82 0%,#e88fb0 55%,#cfae82 100%)}
.p-mac{background:linear-gradient(180deg,#c9a878 0%,#e8993a 55%,#c9a878 100%)}
.p-butter{background:linear-gradient(180deg,#c9a878 0%,#8fb3d6 55%,#c9a878 100%)}
.arrow{position:absolute;top:200px}
.arrow.prev{left:58px}
.arrow.next{left:1122px}

/* quick links */
.quick{display:flex;width:1050px;margin:0 auto;height:150px}
.quick-item{background:var(--box);display:flex;flex-direction:column;align-items:center;justify-content:center;gap:14px;font-size:22px;font-weight:700;color:#444}
.quick-item.info{width:332px}
.quick-item.group{width:386px;background:var(--box-active)}
.quick-item.recruit{width:332px}

/* newsletter */
.newsletter{position:absolute;left:0;top:2028px;width:1200px;height:90px;background:var(--green-dark);display:flex;align-items:center;justify-content:center;gap:28px}
.newsletter h2{color:#fff;font-size:35px;font-weight:700}
.signup{display:flex}
.signup .field{width:347px;height:48px;background:#fff;font-size:13px;color:#333;padding-left:15px;line-height:48px}
.signup .go{width:48px;height:48px;background:var(--orange);display:flex;align-items:center;justify-content:center}

/* footer */
.site-footer{position:absolute;left:0;top:2118px;width:1200px;height:232px;background:var(--footer);color:var(--footer-text);font-size:12.5px}
.f-brand{position:absolute;left:75px;top:45px;display:flex;align-items:center;gap:8px;color:#fff;font-weight:900;font-size:20px;letter-spacing:1px;line-height:1.1}
.f-brand .dot{width:18px;height:18px;border-radius:50%;background:#fff}
.copy{position:absolute;left:75px;top:141px;line-height:1.6;color:#bbb}
.f-col{position:absolute;top:38px}
.f-col h4{color:#fff;font-size:14px;font-weight:700;text-transform:uppercase;margin-bottom:12px}
.f-col li{list-style:none;line-height:28px}
.sitemap{left:338px;width:280px}
.sitemap ul{display:grid;grid-template-columns:132px 140px}
.contact{left:633px;width:240px}
.contact .addr{line-height:23px;margin-bottom:4px}
.contact .row{display:flex;align-items:center;gap:14px;line-height:23px}
.hours{left:902px;width:240px}
.hours p{margin-bottom:26px}
.socials{display:flex;gap:18px;margin-top:-2px}
.socials span{width:20px;height:20px;border-radius:50%;background:#cfcfcf}
</style>
</head>
<body>

<header class="site-header">
  <div class="brand"><span class="brand-dot"></span><span class="brand-name">BRINDALE<br>TRADING</span></div>
  <div class="top-phone">
    <svg width="16" height="16" viewBox="0 0 24 24"><path fill="#2f7a1f" d="M6.6 10.8a15.1 15.1 0 0 0 6.6 6.6l2.2-2.2a1 1 0 0 1 1-.25 11.4 11.4 0 0 0 3.6.57 1 1 0 0 1 1 1V20a1 1 0 0 1-1 1A17 17 0 0 1 3 4a1 1 0 0 1 1-1h3.5a1 1 0 0 1 1 1c0 1.25.2 2.45.57 3.57a1 1 0 0 1-.25 1z"/></svg>
    (808) 555 - 0142
  </div>
  <div class="lang"><span class="flag"></span>EN
    <svg width="8" height="6" viewBox="0 0 8 6"><path d="M1 1l3 3 3-3" stroke="#666" fill="none" stroke-width="1.3"/></svg>
  </div>
  <nav class="main-nav">
    <a class="active" href="#">Home</a><a href="#">About Us</a><a href="#">Products</a><a href="#">Business Contents</a><a href="#">Suppliers</a><a href="#">Online Shopping</a><a href="#">Recruit</a><a href="#">Contact Us</a>
  </nav>
</header>

<section class="hero">
  <div class="hero-photo" role="img" aria-label="Row of kraft paper pancake mix bags in assorted flavours"></div>
  <div class="hero-text">
    <h1 class="hero-title">Rely on businees expertin Hawaii.</h1>
    <p class="hero-sub">Based in Honolulu, Hawaii, based on the concept of "Made in Hawaii", we are working on manufacturing with local companies.</p>
  </div>
  <div class="dots"><span class="on"></span><span></span><span></span><span></span></div>
</section>

<section class="about">
  <h2>About Our Company</h2>
  <h3>The Souvenir you Want is Sure to be found Made in Hawaii's Gourmet Item</h3>
  <p>"Corvel Picks" where premium gourmet items developed by Japanese staff to match the Japanese taste are repeated while repeating trial and error with local companies in Hawaii. Researching high-quality souvenirs and making unique "Made in Hawaii" goods that shape "I hope there is such a product" is popular among souvenirs. We devised measures to make it easy to carry packages, and also recommended for bulk purchase such as balamaki souvenirs. The popular pancake mix only dissolves in water, and finished fluffy pancake.</p>
  <a class="btn" href="#">READ MORE</a>
</section>

<section class="services">
  <div class="service-row">
    <div class="service food" role="img" aria-label="Packaged Hawaiian food products on a table">Planning &amp; manufacturing sales of Hawaiian special food</div>
    <div class="service catering" role="img" aria-label="Bowl of noodle soup">Catering Business</div>
    <div class="service marketing" role="img" aria-label="Team meeting at an office desk">New product planning &amp; marketing</div>
  </div>
</section>

<section class="products">
  <h2>Our Products</h2>
  <svg class="arrow prev" width="20" height="28" viewBox="0 0 20 28"><path d="M15 3L5 14l10 11" stroke="#444" stroke-width="4" fill="none"/></svg>
  <div class="product-row">
    <div class="product"><div class="product-shot p-banana" role="img" aria-label="Banana pancake mix bag"></div><div class="product-name">Banana Taste</div></div>
    <div class="product"><div class="product-shot p-acai" role="img" aria-label="Acai pancake mix bag"></div><div class="product-name">Asai Taste</div></div>
    <div class="product"><div class="product-shot p-mac" role="img" aria-label="Macadamia nut pancake mix bag"></div><div class="product-name">Macadamia Nut aste</div></div>
    <div class="product"><div class="product-shot p-butter" role="img" aria-label="Buttermilk pancake mix bag"></div><div class="product-name">Butter Milk Taste</div></div>
  </div>
  <svg class="arrow next" width="20" height="28" viewBox="0 0 20 28"><path d="M5 3l10 11L5 25" stroke="#444" stroke-width="4" fill="none"/></svg>
</section>

<section class="quick">
  <div class="quick-item info">
    <svg width="40" height="48" viewBox="0 0 40 48"><path d="M2 2h24l12 12v32H2z" fill="#333"/><path d="M26 2v12h12" fill="#777"/><rect x="9" y="22" width="22" height="3" fill="#ededed"/><rect x="9" y="29" width="22" height="3" fill="#ededed"/><rect x="9" y="36" width="22" height="3" fill="#ededed"/></svg>
    Information
  </div>
  <div class="quick-item group">
    <svg width="54" height="46" viewBox="0 0 54 46"><circle cx="27" cy="11" r="9" fill="#333"/><circle cx="10" cy="15" r="6" fill="#333"/><circle cx="44" cy="15" r="6" fill="#333"/><path d="M13 44c0-12 6-20 14-20s14 8 14 20z" fill="#333"/><path d="M0 40c0-9 4-16 10-16 3 0 5 1 6 3-3 4-5 8-5 13z" fill="#333"/><path d="M54 40c0-9-4-16-10-16-3 0-5 1-6 3 3 4 5 8 5 13z" fill="#333"/></svg>
    Group Company
  </div>
  <div class="quick-item recruit">
    <svg width="50" height="44" viewBox="0 0 50 44"><rect x="17" y="2" width="16" height="8" rx="2" fill="none" stroke="#333" stroke-width="3"/><rect x="2" y="10" width="46" height="32" rx="4" fill="#333"/><rect x="11" y="10" width="3" height="32" fill="#ededed"/><rect x="36" y="10" width="3" height="32" fill="#ededed"/></svg>
    Recruit
  </div>
</section>

<section class="newsletter">
  <h2>Newsletter Sign Up</h2>
  <div class="signup">
    <div class="field">Enter Email Address</div>
    <div class="go"><svg width="12" height="18" viewBox="0 0 12 18"><path d="M2 2l7 7-7 7" stroke="#fff" stroke-width="3" fill="none"/></svg></div>
  </div>
</section>

<footer class="site-footer">
  <div class="f-brand"><span class="dot"></span>BRINDALE<br>TRADING</div>
  <div class="copy">Copyright © 2018 Brindale Trading<br>All rights reserved.</div>
  <div class="f-col sitemap">
    <h4>Site Map</h4>
    <ul><li>Home</li><li>Suppliers</li><li>About Us</li><li>Online Shopping</li><li>Products</li><li>Recruit</li><li>Business Contents</li><li>Contact Us</li></ul>
  </div>
  <div class="f-col contact">
    <h4>Contact Info</h4>
    <p class="addr">1470 Palena Lane 305,<br>Honolulu HI 96817</p>
    <div class="row"><svg width="10" height="10" viewBox="0 0 24 24"><path fill="#ccc" d="M6.6 10.8a15.1 15.1 0 0 0 6.6 6.6l2.2-2.2a1 1 0 0 1 1-.25 11.4 11.4 0 0 0 3.6.57 1 1 0 0 1 1 1V20a1 1 0 0 1-1 1A17 17 0 0 1 3 4a1 1 0 0 1 1-1h3.5a1 1 0 0 1 1 1c0 1.25.2 2.45.57 3.57a1 1 0 0 1-.25 1z"/></svg>(808) 555 - 0142</div>
    <div class="row"><svg width="10" height="10" viewBox="0 0 10 10"><rect x="1" y="3" width="8" height="6" fill="#ccc"/><rect x="3" y="0" width="4" height="3" fill="#ccc"/></svg>(808) 555-0178</div>
    <div class="row"><svg width="10" height="8" viewBox="0 0 10 8"><rect width="10" height="8" fill="#ccc"/><path d="M0 0l5 4 5-4" stroke="#333" fill="none"/></svg>info@brindaleads.com</div>
  </div>
  <div class="f-col hours">
    <h4>Office Hours</h4>
    <p>Mon - Fri: 8:00 am - 4:45 pm</p>
    <h4>Follow Us</h4>
    <div class="socials"><span></span><span></span><span></span><span></span><span></span></div>
  </div>
</footer>

</body>
</html>
```